Business card design for my company.
I would like the card's background colour to be black. You can also see our web site to get an idea of our brand. https://www.tmwhomecrafting.com.au/
- Name
- Email

```html
<!DOCTYPE html>
<html lang="en">
<head>
<meta charset="utf-8">
<title>TMW Home Crafting – Business Card</title>
<link rel="stylesheet" href="https://fonts.googleapis.com/css2?family=Roboto:wght@400;500;700&display=swap">
<style>
  :root {
    --stage: #2a2a2a;
    --card-black: #1d1d1f;
    --card-white: #f6f6f4;
    --ink: #111111;
    --green: #0f9a48;
    --muted: #cfcfcf;
  }
  * { box-sizing: border-box; margin: 0; padding: 0; }
  html, body { width: 1200px; height: 852px; overflow: hidden; }
  body {
    background: var(--stage);
    font-family: "Roboto", Arial, sans-serif;
    position: relative;
  }
  .card {
    position: absolute;
    top: 266px;
    width: 520px;
    height: 320px;
    border-radius: 22px;
    overflow: hidden;
    border-bottom: 5px solid var(--green);
  }
  .card--back { left: 50px; background: var(--card-black); }
  .card--front { left: 630px; background: var(--card-white); }

  /* Back */
  .back__brand {
    position: absolute; left: 0; right: 0; top: 120px;
    display: flex; align-items: center; justify-content: center; gap: 12px;
    color: #3a3a3c; font-weight: 700; font-size: 30px; letter-spacing: 3px;
  }
  .brand-square { width: 16px; height: 16px; background: currentColor; display: inline-block; flex: none; }
  .back__web {
    position: absolute; left: 0; right: 0; bottom: 30px;
    text-align: center; color: var(--muted); font-size: 14px; letter-spacing: .3px;
  }

  /* Front */
  .front__art { position: absolute; inset: 0; width: 100%; height: 100%; }
  .front__person { position: absolute; right: 54px; top: 28px; text-align: right; }
  .person__name { color: var(--green); font-weight: 700; font-size: 20px; }
  .person__role { color: var(--ink); font-size: 12px; margin-top: 2px; }
  .front__brand {
    position: absolute; left: 30px; top: 118px;
    display: flex; align-items: center; gap: 10px;
    color: var(--ink); font-weight: 700; font-size: 20px; letter-spacing: 2px;
  }
  .front__brand .brand-square { background: var(--green); }
  .contact {
    position: absolute; right: 26px; top: 162px;
    list-style: none; color: #ffffff; font-size: 12.5px; line-height: 19px;
  }
  .contact li { display: flex; justify-content: flex-end; align-items: center; gap: 8px; }
  .contact svg { width: 11px; height: 11px; fill: var(--green); flex: none; }
</style>
</head>
<body>
  <section class="card card--back">
    <div class="back__brand"><span class="brand-square"></span>TMW HOME CRAFTING</div>
    <p class="back__web">www.tmwhomecrafting.com.au</p>
  </section>

  <section class="card card--front">
    <svg class="front__art" viewBox="0 0 520 320" preserveAspectRatio="none" aria-hidden="true">
      <circle cx="520" cy="20" r="22" fill="var(--green)"/>
      <path d="M520,92 C420,97 330,120 280,168 C230,218 150,268 0,284 L0,320 L520,320 Z" fill="var(--ink)"/>
      <path d="M520,80 C415,85 318,110 266,158 C218,206 140,256 20,272" fill="none" stroke="var(--green)" stroke-width="4"/>
      <path d="M0,292 C150,296 300,304 520,290 L520,306 C330,316 170,310 0,310 Z" fill="var(--green)"/>
    </svg>

    <div class="front__person">
      <p class="person__name">Neil Harcourt</p>
      <p class="person__role">General Manager</p>
    </div>

    <div class="front__brand"><span class="brand-square"></span>TMW HOME CRAFTING</div>

    <ul class="contact">
      <li>0400 555 018
        <svg viewBox="0 0 24 24"><path d="M6.6 10.8a15 15 0 0 0 6.6 6.6l2.2-2.2c.3-.3.7-.4 1-.2 1.1.4 2.3.6 3.6.6.6 0 1 .4 1 1V20c0 .6-.4 1-1 1A17 17 0 0 1 3 4c0-.6.4-1 1-1h3.5c.6 0 1 .4 1 1 0 1.3.2 2.5.6 3.6.1.3 0 .7-.2 1z"/></svg></li>
      <li>tmwhomecrafting.com.au
        <svg viewBox="0 0 24 24"><path d="M2 5h20v14H2z M2 5l10 8 10-8" fill="none" stroke="var(--green)" stroke-width="2.5"/></svg></li>
      <li>Launceston, Tasmania, Australia
        <svg viewBox="0 0 24 24"><circle cx="12" cy="12" r="9" fill="none" stroke="var(--green)" stroke-width="2.5"/><path d="M3 12h18M12 3c3 3 3 15 0 18M12 3c-3 3-3 15 0 18" fill="none" stroke="var(--green)" stroke-width="2"/></svg></li>
      <li>info@tmwhomecrafting.com.au
        <svg viewBox="0 0 24 24"><path d="M12 2a7 7 0 0 0-7 7c0 5 7 13 7 13s7-8 7-13a7 7 0 0 0-7-7zm0 9.5A2.5 2.5 0 1 1 12 6.5a2.5 2.5 0 0 1 0 5z"/></svg></li>
    </ul>
  </section>
</body>
</html>
```